BrimFalcon Business Cards

We have a defined brand. Please visit our website to get a feel for the product and the color pallets. www.brimfalcon-example.com

We need an updated, world class business card design. (See the attached existing card design). Please utilize BOTH sides of the card as shown and be creative with the layout. I do want the horse head icon to be positioned as it is with the existing card.

The remainder of the layout can be customized and I also want it vertically oriented.

Attached are the logo files and please use the colors as follows:
Green - #A5CE39
Tan - #CDBD99
Black

Feel free to play with the colors.

```html
<!DOCTYPE html>
<html lang="en">
<head>
<meta charset="utf-8">
<title>BrimFalcon Business Cards</title>
<link href="https://fonts.googleapis.com/css2?family=Rubik:wght@400;500;700&display=swap" rel="stylesheet">
<style>
  :root {
    --brand-green: #a5ce39;
    --brand-black: #111111;
    --text-grey: #4a4a4a;
    --card-white: #ffffff;
    --stage: #e9e9e7;
  }
  * { box-sizing: border-box; margin: 0; padding: 0; }
  html, body { width: 1200px; height: 941px; overflow: hidden; }
  body {
    background: var(--stage);
    font-family: "Rubik", sans-serif;
    position: relative;
  }
  .card {
    position: absolute;
    top: 120px;
    width: 400px;
    height: 700px;
    box-shadow: 0 6px 24px rgba(0,0,0,0.12);
  }
  .card--front { left: 170px; background: var(--card-white); }
  .card--back { left: 630px; background: var(--brand-green); }

  .wordmark {
    position: absolute;
    display: flex;
    align-items: center;
    gap: 12px;
    font-weight: 700;
    color: var(--brand-black);
  }
  .card--front .wordmark { top: 70px; left: 44px; font-size: 40px; letter-spacing: 1px; }
  .wordmark__dot {
    width: 40px; height: 40px; border-radius: 50%;
    background: var(--brand-black);
  }

  .contact { position: absolute; left: 44px; top: 380px; }
  .contact__name { font-size: 34px; font-weight: 700; color: var(--brand-black); }
  .contact__title { font-size: 17px; font-weight: 500; color: var(--brand-green); margin-top: 2px; }
  .contact__rule { width: 44px; height: 2px; background: var(--brand-green); margin: 22px 0 18px; }
  .contact__lines { font-size: 17px; line-height: 1.3; color: var(--text-grey); }

  .card--back .wordmark {
    top: 150px; left: 0; width: 100%;
    justify-content: center; font-size: 46px; flex-direction: column; gap: 20px;
  }
  .card--back .wordmark__dot { width: 150px; height: 150px; }
  .tagline {
    position: absolute;
    bottom: 70px; right: 44px;
    text-align: right;
    font-size: 26px; font-weight: 700;
    color: var(--brand-black);
  }
</style>
</head>
<body>
  <section class="card card--front">
    <div class="wordmark"><span class="wordmark__dot"></span>BrimFalcon</div>
    <div class="contact">
      <h1 class="contact__name">Dana Merrow</h1>
      <p class="contact__title">President &amp; CEO</p>
      <div class="contact__rule"></div>
      <p class="contact__lines">BrimFalcon Labs LLC<br>Fenwick, Ontario<br>Canada</p>
      <div class="contact__rule"></div>
      <p class="contact__lines">P. 555.014.2290<br>dana@brimfalcon-example.com<br>www.brimfalconlabs-example.com</p>
    </div>
  </section>

  <section class="card card--back">
    <div class="wordmark"><span class="wordmark__dot"></span>BrimFalcon</div>
    <p class="tagline">Motion Redefined</p>
  </section>
</body>
</html>
```